"Vine Hollow Excursions" is a top notch Santa Barbara County Wine Tour company.

We provide scenic, boutique and custom wine tours. I need the card to be clean and classy. I will provide our logo. I would like the logo to cover the back side of the card as an option and would like to see a couple color options other then our signature green and gold. I would like to see some creative options and let the designers come up with options.
I need cards for myself and my team. The final design should communicate "An authentic and boutique wine tour experience"
Please use my website for reference www.vinehollowexcursions.example

Target Market(s)

We have a wide range of clients from millennials to baby boomers

Industry/Entity Type

Tour

Contact Information for Business Card

Contact info:
Dale Morton
805-219-6384
info@vinehollowexcursions.example
vinehollowexcursions.example

Colors

Designer to choose colors to be used in the design.

Requirements
Must have
• my logo
Nice to have
• *I would like to have the backside side with the logo and the company statement
• "An authentic and boutique wine tour experience" as an option.
• *I would also like to see what the designers can create!
• *I would like to see an option that incorporates or social: instagram, yelp, Tour Advisor
Should not have
• I do not want it too busy.

```html
<!DOCTYPE html>
<html lang="en">
<head>
<meta charset="utf-8">
<title>Vine Hollow Excursions – Business Card</title>
<link rel="stylesheet" href="https://fonts.googleapis.com/css2?family=Cinzel:wght@500&family=Montserrat:wght@400;600&display=swap">
<style>
  :root {
    --stage: #1c1d1f;
    --green: #4a7a52;
    --green-deep: #3b6444;
    --charcoal: #30383a;
    --charcoal-deep: #1f2527;
    --gold: #a47a3a;
    --white: #ffffff;
    --logo-green: #2f6a43;
    --ink-light: #e8ecec;
  }
  * { margin: 0; padding: 0; box-sizing: border-box; }
  html, body { width: 1200px; height: 900px; overflow: hidden; background: var(--stage); }
  .canvas { position: relative; width: 1200px; height: 900px; }

  .card {
    position: absolute;
    width: 630px;
    height: 360px;
    border-radius: 22px;
    overflow: hidden;
    box-shadow: 0 14px 30px rgba(0,0,0,0.45);
  }

  /* Front */
  .card-front {
    left: 80px; top: 70px;
    background: linear-gradient(135deg, var(--green-deep), var(--green) 55%, var(--green-deep));
    display: flex; align-items: center; justify-content: center;
  }
  .brand { display: flex; align-items: center; gap: 12px; }
  .brand-dot { width: 14px; height: 14px; border-radius: 50%; flex: none; }
  .brand-name {
    font-family: "Cinzel", serif;
    font-weight: 500;
    letter-spacing: 1px;
  }
  .card-front .brand-dot { background: var(--white); }
  .card-front .brand-name { color: var(--white); font-size: 30px; }

  /* Back */
  .card-back {
    left: 490px; top: 470px;
    background: linear-gradient(160deg, var(--charcoal), var(--charcoal-deep));
  }
  .card-back .swoosh { position: absolute; inset: 0; }
  .card-back .brand { position: absolute; left: 365px; top: 150px; width: 240px; }
  .card-back .brand-dot { background: var(--logo-green); width: 10px; height: 10px; }
  .card-back .brand-name { color: var(--logo-green); font-size: 19px; line-height: 1.25; }

  .contact {
    position: absolute; left: 46px; top: 150px;
    font-family: "Montserrat", sans-serif;
    color: var(--ink-light);
  }
  .person-name { font-weight: 600; font-size: 22px; letter-spacing: 0.5px; color: var(--white); }
  .person-role { font-weight: 600; font-size: 17px; color: var(--gold); margin-bottom: 12px; }
  .contact-list { list-style: none; font-size: 12px; line-height: 17px; }
  .contact-list li { display: flex; align-items: center; gap: 9px; white-space: nowrap; }
  .contact-list li::before {
    content: ""; width: 9px; height: 9px; border-radius: 50%;
    background: var(--gold); flex: none;
  }
  .contact-list strong { font-weight: 600; }
</style>
</head>
<body>
<main class="canvas">
  <section class="card card-front" aria-label="Card front">
    <div class="brand">
      <span class="brand-dot"></span>
      <span class="brand-name">Vine Hollow Excursions</span>
    </div>
  </section>

  <section class="card card-back" aria-label="Card back">
    <svg class="swoosh" width="630" height="360" viewBox="0 0 630 360" aria-hidden="true">
      <circle cx="534" cy="128" r="242" fill="none" stroke="var(--gold)" stroke-width="3"/>
      <circle cx="541" cy="128" r="234" fill="var(--gold)"/>
      <circle cx="548" cy="124" r="226" fill="var(--white)"/>
    </svg>
    <div class="brand">
      <span class="brand-dot"></span>
      <span class="brand-name">Vine Hollow Excursions</span>
    </div>
    <div class="contact">
      <p class="person-name">DALE MORTON</p>
      <p class="person-role">Tour Advisor</p>
      <ul class="contact-list">
        <li><span>805-219-6384</span></li>
        <li><span>info@vinehollowexcursions.example</span></li>
        <li><span>www.<strong>vinehollowexcursions</strong>.example</span></li>
        <li><span>/vinehollowexcursions</span></li>
        <li><span>@vinehollowexcursions</span></li>
        <li><span>/biz/vinehollowexcursions</span></li>
        <li><span>@sbvinehollow</span></li>
      </ul>
    </div>
  </section>
</main>
</body>
</html>
```